Silver Bloom Marisol's Cleaning Service Business Cards Project

A business card with all contact details with logo design on there (already have a logo) eye catching Logo and contact info on one side, full logo on the back, must target upper class residential and corporate companies, fitness companies, still keep it on the feminine side of things , must look elegant

Target Market(s)

Upper class homes and corporate companies

Industry/Entity Type

Cleaning Service

Contact Information for Business Card

Name: Marisol Quenby
Position: Director
ABN: 31647209853
Email: marisolssilvercleaning@tidymail.example
Number: 0417906354

Font styles to use
Decorative

Colors

Designer to choose colors to be used in the design.

Requirements
Must have
• Available Sydney Wide, contact info and logo on one side, full logo on the back
Nice to have
• Professional appearance
Should not have
• Cheap advert looking stuff

```html
<!DOCTYPE html>
<html lang="en">
<head>
<meta charset="utf-8">
<title>Silver Bloom Business Cards</title>
<link rel="stylesheet" href="https://fonts.googleapis.com/css2?family=Lustria&family=Lato:wght@400&display=swap">
<style>
  :root {
    --backdrop: #676767;
    --card-white: #ffffff;
    --card-navy: #2e3240;
    --ink: #262a36;
    --accent-teal: #38e0d4;
    --muted-edge: #5a5a5a;
  }
  * { box-sizing: border-box; margin: 0; padding: 0; }
  html, body {
    width: 1200px; height: 802px; overflow: hidden;
    background: var(--backdrop);
  }
  .canvas { position: relative; width: 1200px; height: 802px; }
  .card {
    position: absolute; top: 274px; width: 443px; height: 265px;
    box-shadow: 0 10px 0 var(--muted-edge), 0 18px 30px rgba(0,0,0,.25);
  }
  .card-front { left: 136px; background: var(--card-white); color: var(--ink); }
  .card-back { left: 624px; background: var(--card-navy); }

  .brand-name {
    position: absolute; left: 31px; top: 38px;
    font-family: "Lustria", serif; font-size: 32px; letter-spacing: .5px;
    font-weight: 400; color: var(--ink);
  }
  .contact { position: absolute; left: 31px; top: 140px; font-family: "Lato", sans-serif; }
  .person-name { font-family: "Lustria", serif; font-size: 18px; letter-spacing: .3px; line-height: 1; }
  .person-role { font-size: 13px; margin-top: 4px; }
  .abn { font-size: 13px; margin-top: 12px; }
  .contact-lines { margin-top: 12px; font-size: 12.5px; line-height: 16px; }
  .contact-line { display: flex; align-items: center; gap: 5px; }
  .contact-line svg { width: 10px; height: 10px; fill: var(--ink); }

  .back-mark {
    position: absolute; left: 50%; top: 62px; transform: translateX(-50%);
    width: 58px; height: 58px; border-radius: 50%;
    border: 2px solid var(--accent-teal);
  }
  .back-name {
    position: absolute; left: 0; right: 0; top: 170px; text-align: center;
    font-family: "Lustria", serif; font-size: 24px; letter-spacing: .5px;
    color: var(--accent-teal);
  }
</style>
</head>
<body>
<main class="canvas">
  <section class="card card-front" aria-label="Business card front">
    <h1 class="brand-name">SILVER BLOOM</h1>
    <div class="contact">
      <p class="person-name">MARISOL QUENBY</p>
      <p class="person-role">Director</p>
      <p class="abn">ABN: 31647209853</p>
      <div class="contact-lines">
        <p class="contact-line">
          <svg viewBox="0 0 10 10" aria-hidden="true"><path d="M1 3.2C1 2 2 1.5 5 1.5S9 2 9 3.2V4H7V3H3v1H1zM2.2 8.5 3 5h4l.8 3.5z"/></svg>
          0417906354
        </p>
        <p class="contact-line">
          <svg viewBox="0 0 10 10" aria-hidden="true"><path d="M1 2h8v6H1zM1.6 2.6 5 5.4l3.4-2.8V3L5 6 1.6 3z" fill-rule="evenodd"/></svg>
          marisolssilvercleaning@tidymail.example
        </p>
      </div>
    </div>
  </section>

  <section class="card card-back" aria-label="Business card back">
    <span class="back-mark" aria-hidden="true"></span>
    <p class="back-name">SILVER BLOOM</p>
  </section>
</main>
</body>
</html>
```